High-Converting Facebook Ads for Portals Drapes & Louvres (6 Products)

We are looking for a graphic designer to create high-quality Facebook & Instagram ads for our business: Portals Drapes and Louvres (Melbourne, Australia).

We require 6 separate ad designs, each for a different product:

Zipscreen Blinds

Outdoor Awnings

Plantation Shutters

Roller Shutters

Security Doors

Roller Blinds & Sheer Curtains

Ad Specifications:

Sizes:

1440 x 1800 px (4:5 ratio)

1080 x 1080 px (1:1 ratio)

1080 x 1920 px (9:16 ratio for Stories/Reels)

Format: PNG (high resolution, not blurry)

Designed specifically for Meta (Facebook/Instagram ads)

Mobile-friendly layout (clear, easy to read)

Style:

Bold, sales-driven, retail-style ads (NOT minimal)

Eye-catching and designed to generate leads

Clean, professional layout

Similar to promotional home improvement ads

Brand Colours:

Red: #E31E24

Blue: #0072BC

White backgrounds

Each ad must include:

“SALE NOW ON” banner at top

Our showroom address:
482 Upper Wattleby Road, Kestrel Heights (must be fully visible, not cut off)

Phone number: 9471 2658

Our logo (provided)

Badge: “Celebrating 13 YEARS in Business” (must be clean and readable)

Call to Action:

For 5 ads: “Book a FREE quote TODAY!”

For Security Doors ad: “ORDER NOW”

Offers / Pricing:

Most products: “UP TO 40% OFF”

Plantation Shutters: “FROM $299/sqm”

Security Doors: “FROM $750”

Content for each ad (examples):

Zipscreen Blinds:

Made to Measure

Fully Installed

Wind, Sun & Insect Protection

Outdoor Awnings:

Reduce Heat & Glare

Energy Saving

Custom Made

Plantation Shutters:

Modern & Elegant

Light & Privacy Control

Durable & Easy Care

Roller Shutters:

Security Protection

Block Heat & Noise

Total Light Control

Security Doors:

3 Point Locking

Premium Mesh

Custom Made

Blinds & Sheers:

Huge Range of Fabrics

Modern Soft Finish

Perfect for Any Room

Important Notes:

All text must be sharp and easy to read (no blur)

Layout must be balanced and not overcrowded

Ensure no text is cut off (especially address and headings)

Badge text must be straight and professional (no distortion)

Use high-quality, relevant images (we will provide references)

Goal:
Create ads that look professional, trustworthy, and generate enquiries/bookings for in-home quotes.

We are open to creative ideas but want a strong, bold retail-style ad that converts.
I have uploaed chatgpt mocks

Target Market(s)

Homeowners in Melbourne, Australia (typically aged 30–65) looking to improve their homes with blinds, shutters, awnings and security doors. Mid to high income households focused on quality, security, and modern home upgrades.

Industry/Entity Type

Home Improvement / Construction / Retail

Font styles to use
Sans Serif

Requirements
Must have
• Clear, bold and easy-to-read text (must be readable on mobile) High-quality, non-blurry design Strong “SALE” style layout (retail promotional look) Proper spacing (no overcrowded designs) All key info visible (address must NOT be cut off) Correct pricing and offers included Clean “13 YEARS” badge (no distortion or curved text) Consistent branding across all 6 ads
Nice to have
• Modern, slightly premium feel while still being bold Good use of contrast (red/blue/white) Subtle shadows or layering to improve depth Clean use of icons or bullet points Strong hierarchy (headline → benefits → offer → CTA) Variations in layout for testing different ad styles
Should not have
• Minimal or plain designs (we want bold, sales-driven ads) Hard-to-read fonts or script fonts Low-quality or blurry images Overcrowded layouts with too much text Important text cut off (especially address or headings) Overuse of effects or “cheap” looking graphics Yellow-heavy colour schemes (must follow brand colours)

```html
<!DOCTYPE html>
<html lang="en">
<head>
<meta charset="utf-8">
<title>Portals Drapes & Louvres — 1080 x 1080 Sale Ads</title>
<link href="https://fonts.googleapis.com/css2?family=Poppins:wght@400;500;600;700;800&family=Oswald:wght@500;600&display=swap" rel="stylesheet">
<style>
  :root{
    --board:#333333;
    --board-title:#bdbdbd;
    --brand-red:#E31E24;
    --brand-blue:#0072BC;
    --white:#ffffff;
    --gold-1:#f3cf5a;
    --gold-2:#c99a1d;
    --gold-ink:#4a3605;
  }
  *{box-sizing:border-box;margin:0;padding:0}
  html,body{width:1200px;height:1000px;overflow:hidden;background:var(--board)}
  body{position:relative;font-family:"Poppins",sans-serif}

  .board-title{position:absolute;top:44px;left:0;width:1200px;text-align:center;
    font-weight:400;font-size:46px;letter-spacing:1px;color:var(--board-title)}

  .ad{position:absolute;width:259px;height:259px;overflow:hidden;background:var(--white)}
  .col-1{left:177px}.col-2{left:470px}.col-3{left:764px}
  .row-1{top:216px}.row-2{top:513px}

  .photo{position:absolute;left:0;top:47px;width:100%;bottom:0}

  .header{position:absolute;left:0;top:0;width:100%;height:47px;background:var(--white);z-index:2}
  .brand{position:absolute;left:10px;top:8px;width:66px;text-align:center}
  .brand-mark{display:block;width:11px;height:11px;margin:0 auto 2px;background:var(--brand-red)}
  .brand-name{display:block;font-weight:700;font-size:7.5px;line-height:1.05;color:var(--brand-blue)}
  .sale-title{position:absolute;left:86px;top:10px;font-weight:700;font-size:22px;line-height:1;color:var(--brand-blue);white-space:nowrap}

  .address-band{position:absolute;left:0;top:47px;width:100%;height:20px;background:var(--brand-red);
    clip-path:polygon(0 0,100% 0,98% 100%,2% 100%);z-index:3;display:flex;align-items:center;justify-content:center;gap:4px;
    color:var(--white);font-weight:600;font-size:9.6px;white-space:nowrap}
  .phone-band{position:absolute;left:104px;right:0;top:70px;height:25px;background:var(--brand-blue);
    clip-path:polygon(7% 0,100% 0,100% 100%,14% 100%);z-index:3;display:flex;align-items:center;justify-content:flex-end;gap:8px;padding-right:11px;
    color:var(--white);font-weight:700;font-size:19px;letter-spacing:.3px}
  .icon{width:9px;height:9px;fill:currentColor;flex:none}
  .phone-band .icon{width:10px;height:10px}

  .badge{position:absolute;top:65px;width:58px;height:58px;border-radius:50%;z-index:4;
    background:radial-gradient(circle at 40% 35%,var(--gold-1),var(--gold-2));
    border:2px solid var(--white);box-shadow:0 1px 3px rgba(0,0,0,.4);
    display:flex;flex-direction:column;align-items:center;justify-content:center;color:var(--gold-ink);text-align:center;line-height:1}
  .badge.at-left{left:5px}.badge.at-mid{left:40px}
  .badge-top{font-size:4px;font-weight:600}
  .badge-num{font-size:22px;font-weight:800;margin:1px 0 0}
  .badge-unit{font-size:7px;font-weight:700}
  .badge-sub{font-size:3.8px;font-weight:600;letter-spacing:.5px;margin-top:1px}

  .panel{position:absolute;background:var(--brand-blue);z-index:1}
  .product{position:absolute;font-family:"Oswald",sans-serif;font-weight:600;color:var(--white);font-size:12.5px;letter-spacing:-.2px;z-index:3;white-space:nowrap}
  .benefits{position:absolute;list-style:none;z-index:3;color:var(--white);font-weight:600;font-size:7.6px}
  .benefits li{display:flex;align-items:center;gap:4px;height:12px;white-space:nowrap}
  .benefits .icon{width:7px;height:7px}
  .benefits.large{font-size:9.4px}
  .benefits.large li{height:15px}
  .benefits.large .icon{width:9px;height:9px}

  .offer{position:absolute;z-index:3;color:var(--white);line-height:1}
  .offer-lead{display:block;font-weight:500;font-size:20px}
  .offer-value{display:block;margin-top:9px;font-size:17px;font-weight:500}
  .offer-value b{font-size:27px;font-weight:700}

  .cta{position:absolute;z-index:4;background:var(--brand-red);color:var(--white);font-weight:700;text-align:center;
    border-radius:18px;border:1.5px solid rgba(255,255,255,.85);box-shadow:0 2px 4px rgba(0,0,0,.3);
    display:flex;flex-direction:column;justify-content:center;line-height:1.2}

  /* zipscreen */
  .zip-offer{position:absolute;left:100px;top:133px;z-index:3;font-weight:700;font-size:19px;line-height:1.18;text-align:center;color:var(--white)}
  .zip-offer .hot{color:var(--brand-red)}
</style>
</head>
<body>
<svg width="0" height="0" style="position:absolute" aria-hidden="true">
  <defs>
    <symbol id="pin" viewBox="0 0 24 24"><path d="M12 2a7 7 0 0 0-7 7c0 5 7 13 7 13s7-8 7-13a7 7 0 0 0-7-7zm0 9.5A2.5 2.5 0 1 1 12 6.5a2.5 2.5 0 0 1 0 5z"/></symbol>
    <symbol id="phone" viewBox="0 0 24 24"><path d="M6.6 10.8a15 15 0 0 0 6.6 6.6l2.2-2.2a1 1 0 0 1 1-.25 11.4 11.4 0 0 0 3.6.57 1 1 0 0 1 1 1V20a1 1 0 0 1-1 1A17 17 0 0 1 3 4a1 1 0 0 1 1-1h3.5a1 1 0 0 1 1 1c0 1.25.2 2.45.57 3.6a1 1 0 0 1-.25 1z"/></symbol>
    <symbol id="tick" viewBox="0 0 24 24"><circle cx="12" cy="12" r="9.5" fill="none" stroke="currentColor" stroke-width="2.4"/><path d="M7.5 12.3l3 3 6-6.5" fill="none" stroke="currentColor" stroke-width="2.6" stroke-linecap="round" stroke-linejoin="round"/></symbol>
  </defs>
</svg>

<h1 class="board-title">1080 x 1080</h1>

<!-- Zipscreen Blinds -->
<section class="ad col-1 row-1">
  <div class="photo" role="img" aria-label="Brick home alfresco area with dark zipscreen blinds lowered" style="background:linear-gradient(160deg,#d9dde0 0%,#8a5a48 38%,#2e2e30 60%,#1f6fae 90%)"></div>
  <header class="header"><div class="brand"><span class="brand-mark"></span><span class="brand-name">Portals Drapes<br>&amp; Louvres</span></div><p class="sale-title">SALE NOW ON</p></header>
  <div class="address-band"><svg class="icon"><use href="#pin"/></svg>482 Upper Wattleby Road, Kestrel Heights</div>
  <div class="phone-band"><svg class="icon"><use href="#phone"/></svg>9471 2658</div>
  <div class="badge at-left"><span class="badge-top">CELEBRATING</span><span class="badge-num">13</span><span class="badge-unit">YEARS</span><span class="badge-sub">IN BUSINESS</span></div>
  <p class="zip-offer">UP<br>TO<br><span class="hot">40%</span><br><span class="hot">OFF</span></p>
  <div class="cta" style="left:165px;top:186px;width:83px;height:22px;font-size:6.5px">Book a<span>FREE quote TODAY!</span></div>
  <h2 class="product" style="left:6px;top:204px">ZIPSCREEN BLINDS:</h2>
  <ul class="benefits" style="left:7px;top:216px">
    <li><svg class="icon"><use href="#tick"/></svg>Made to Measure</li>
    <li><svg class="icon"><use href="#tick"/></svg>Fully Installed</li>
    <li><svg class="icon"><use href="#tick"/></svg>Wind, Sun &amp; Insect Protection</li>
  </ul>
</section>

<!-- Outdoor Awnings -->
<section class="ad col-2 row-1">
  <div class="photo" role="img" aria-label="Brick house front with green and white striped outdoor awnings" style="background:linear-gradient(180deg,#5a5048 0%,#8c4a3c 55%,#b9a58f 100%)"></div>
  <header class="header"><div class="brand"><span class="brand-mark"></span><span class="brand-name">Portals Drapes<br>&amp; Louvres</span></div><p class="sale-title">SALE NOW ON</p></header>
  <div class="address-band"><svg class="icon"><use href="#pin"/></svg>482 Upper Wattleby Road, Kestrel Heights</div>
  <div class="phone-band"><svg class="icon"><use href="#phone"/></svg>9471 2658</div>
  <div class="badge at-left"><span class="badge-top">CELEBRATING</span><span class="badge-num">13</span><span class="badge-unit">YEARS</span><span class="badge-sub">IN BUSINESS</span></div>
  <div class="panel" style="left:0;top:192px;width:100%;height:67px"></div>
  <div class="cta" style="left:51px;top:147px;width:163px;height:45px;font-size:13px;border-radius:22px">Book a<span>FREE quote TODAY!</span></div>
  <h2 class="product" style="left:11px;top:202px">OUTDOOR AWNINGS:</h2>
  <ul class="benefits" style="left:13px;top:216px">
    <li><svg class="icon"><use href="#tick"/></svg>Reduce Heat &amp; Glare</li>
    <li><svg class="icon"><use href="#tick"/></svg>Energy Saving</li>
    <li><svg class="icon"><use href="#tick"/></svg>Custom Made</li>
  </ul>
  <p class="offer" style="left:144px;top:198px"><span class="offer-lead">UP TO</span><span class="offer-value"><b>40%</b> OFF</span></p>
</section>

<!-- Plantation Shutters -->
<section class="ad col-3 row-1">
  <div class="photo" role="img" aria-label="Bright bedroom with white plantation shutters on the windows" style="background:linear-gradient(180deg,#e4e6e8 0%,#c8ccd0 60%,#9aa2a8 100%)"></div>
  <header class="header"><div class="brand"><span class="brand-mark"></span><span class="brand-name">Portals Drapes<br>&amp; Louvres</span></div><p class="sale-title">SALE NOW ON</p></header>
  <div class="address-band"><svg class="icon"><use href="#pin"/></svg>482 Upper Wattleby Road, Kestrel Heights</div>
  <div class="phone-band"><svg class="icon"><use href="#phone"/></svg>9471 2658</div>
  <div class="badge at-mid" style="top:63px"><span class="badge-top">CELEBRATING</span><span class="badge-num">13</span><span class="badge-unit">YEARS</span><span class="badge-sub">IN BUSINESS</span></div>
  <div class="panel" style="left:0;top:170px;width:100%;height:89px;clip-path:polygon(0 14%,100% 0,100% 100%,0 100%)"></div>
  <div class="cta" style="left:61px;top:144px;width:137px;height:40px;font-size:11.5px;border-radius:20px">Book a<span>FREE quote TODAY!</span></div>
  <h2 class="product" style="left:13px;top:203px">PLANTATION SHUTTERS:</h2>
  <ul class="benefits" style="left:15px;top:218px">
    <li><svg class="icon"><use href="#tick"/></svg>Modern &amp; Elegant</li>
    <li><svg class="icon"><use href="#tick"/></svg>Light &amp; Privacy Control</li>
    <li><svg class="icon"><use href="#tick"/></svg>Durable &amp; Easy Care</li>
  </ul>
  <p class="offer" style="left:144px;top:198px"><span class="offer-lead">UP TO</span><span class="offer-value"><b>40%</b> OFF</span></p>
</section>

<!-- Roller Shutters -->
<section class="ad col-1 row-2">
  <div class="photo" role="img" aria-label="Modern home facade with grey roller shutters on the windows" style="background:linear-gradient(180deg,#3a3836 0%,#7a6a5c 50%,#9a9890 100%)"></div>
  <header class="header"><div class="brand"><span class="brand-mark"></span><span class="brand-name">Portals Drapes<br>&amp; Louvres</span></div><p class="sale-title">SALE NOW ON</p></header>
  <div class="address-band"><svg class="icon"><use href="#pin"/></svg>482 Upper Wattleby Road, Kestrel Heights</div>
  <div class="phone-band"><svg class="icon"><use href="#phone"/></svg>9471 2658</div>
  <div class="badge at-mid"><span class="badge-top">CELEBRATING</span><span class="badge-num">13</span><span class="badge-unit">YEARS</span><span class="badge-sub">IN BUSINESS</span></div>
  <div class="panel" style="left:0;top:175px;width:100%;height:84px"></div>
  <div class="cta" style="left:60px;top:148px;width:138px;height:37px;font-size:11.5px">Book a<span>FREE quote TODAY!</span></div>
  <h2 class="product" style="left:8px;top:196px;font-size:13.5px">ROLLER SHUTTERS:</h2>
  <ul class="benefits large" style="left:10px;top:212px">
    <li><svg class="icon"><use href="#tick"/></svg>Security Protection</li>
    <li><svg class="icon"><use href="#tick"/></svg>Block Heat &amp; Noise</li>
    <li><svg class="icon"><use href="#tick"/></svg>Total Light Control</li>
  </ul>
  <p class="offer" style="left:144px;top:198px"><span class="offer-lead">UP TO</span><span class="offer-value"><b>40%</b> OFF</span></p>
</section>

<!-- Security Doors -->
<section class="ad col-2 row-2">
  <div class="photo" role="img" aria-label="Charcoal security door with mesh fitted to a home entrance" style="background:linear-gradient(90deg,#e6dcc8 0%,#d8cdb6 45%,#2c3440 55%,#3a4452 100%)"></div>
  <header class="header"><div class="brand"><span class="brand-mark"></span><span class="brand-name">Portals Drapes<br>&amp; Louvres</span></div><p class="sale-title">SALE NOW ON</p></header>
  <div class="address-band"><svg class="icon"><use href="#pin"/></svg>482 Upper Wattleby Road, Kestrel Heights</div>
  <div class="phone-band"><svg class="icon"><use href="#phone"/></svg>9471 2658</div>
  <div class="badge at-mid"><span class="badge-top">CELEBRATING</span><span class="badge-num">13</span><span class="badge-unit">YEARS</span><span class="badge-sub">IN BUSINESS</span></div>
  <div class="panel" style="left:0;top:158px;width:123px;height:101px"></div>
  <div class="cta" style="left:8px;top:136px;width:97px;height:27px;font-size:12px">ORDER NOW</div>
  <h2 class="product" style="left:9px;top:173px;font-size:15px">SECURITY DOORS:</h2>
  <ul class="benefits large" style="left:11px;top:197px">
    <li><svg class="icon"><use href="#tick"/></svg>3 Point Locking</li>
    <li><svg class="icon"><use href="#tick"/></svg>Premium Mesh</li>
    <li><svg class="icon"><use href="#tick"/></svg>Custom Made</li>
  </ul>
  <p class="offer" style="left:144px;top:183px"><span class="offer-lead" style="color:var(--brand-red);font-size:16px">FROM</span><span class="offer-value" style="margin-top:6px"><b style="font-size:29px">$750</b></span></p>
</section>

<!-- Blinds & Sheers -->
<section class="ad col-3 row-2">
  <div class="photo" role="img" aria-label="Living room window with soft grey sheer curtains and blinds" style="background:linear-gradient(90deg,#cfcac2 0%,#8e8880 40%,#b4aea6 70%,#ddd8d0 100%)"></div>
  <header class="header"><div class="brand"><span class="brand-mark"></span><span class="brand-name">Portals Drapes<br>&amp; Louvres</span></div><p class="sale-title">SALE NOW ON</p></header>
  <div class="address-band"><svg class="icon"><use href="#pin"/></svg>482 Upper Wattleby Road, Kestrel Heights</div>
  <div class="phone-band"><svg class="icon"><use href="#phone"/></svg>9471 2658</div>
  <div class="badge at-mid"><span class="badge-top">CELEBRATING</span><span class="badge-num">13</span><span class="badge-unit">YEARS</span><span class="badge-sub">IN BUSINESS</span></div>
  <div class="panel" style="left:0;top:158px;width:100%;height:101px;clip-path:polygon(0 0,100% 10%,100% 100%,0 100%)"></div>
  <div class="cta" style="left:135px;top:165px;width:104px;height:28px;font-size:8px">Book a<span>FREE quote TODAY!</span></div>
  <h2 class="product" style="left:7px;top:172px;font-size:14px">BLINDS &amp; SHEERS:</h2>
  <ul class="benefits large" style="left:8px;top:195px">
    <li><svg class="icon"><use href="#tick"/></svg>Huge Range of Fabrics</li>
    <li><svg class="icon"><use href="#tick"/></svg>Modern Soft Finish</li>
    <li><svg class="icon"><use href="#tick"/></svg>Perfect for Any Room</li>
  </ul>
  <p class="offer" style="left:152px;top:201px"><span class="offer-lead" style="font-size:18px">UP TO</span><span class="offer-value" style="margin-top:7px"><b style="font-size:23px">40% OFF</b></span></p>
</section>
</body>
</html>
```